Global Beard Oil Review Business needs a refresh

topwhiskertonic.net is a global business who's mission is to curate all available beard oils from around the world, review and grade them and present this curated collection to the user of the website.

The scope of this job includes the web site design and the design of a suitable logo to be used in the site header.

The existing site can be seen on http://topwhiskertonic.net, however this is a mock-up only the style and logo should NOT be used. This is to give you an idea of the concept of the site only.

This job is for PSD design only.

See attached design brief for detailed design requirements.
Updates

Project Deadline Extended
Reason: Extending deadline by 5 days to allow for final submissions

Target Market(s)

Men's grooming / retail

Industry/Entity Type

Retail

Number of Pages Required

2 page

Font styles to use
Sans Serif

Requirements
Must have
• 1) Comparison Table
• 2) Side Bar
• 3) Header area
• 4) Photo of Delvin Marsk (attached - can be circular or "cut-out")
• 5) Cool beard-oriented custom design background (e.g., stylistic black/brown on brown/orange beard background. I envision this beard background "drawing" rather than photo based)
• (see attached design requirements for details)
Nice to have
• Signature style writing at top with name "Delvin Marsk"
Should not have
• Do NOT use the look & feel or logo from the existing site.

```html
<!DOCTYPE html>
<html lang="en">
<head>
<meta charset="utf-8">
<title>Top Whisker Tonic — Beard Oil Reviews</title>
<link rel="stylesheet" href="https://fonts.googleapis.com/css2?family=Lato:ital,wght@0,400;0,700;1,400&family=Rufina:wght@400;700&family=Playball&display=swap">
<style>
:root{
  --page-grey:#a9a9a9;
  --parchment:#e6d29c;
  --parchment-dark:#cfb577;
  --brown:#93601f;
  --ink:#222;
  --text:#444;
  --row:#b38b5d;
  --row-alt:#a67d4d;
  --row-line:#8f6a3e;
  --table-head:#2b2b2b;
  --black:#000;
  --white:#fff;
  --footer-text:#ddd;
  --footer-brand:#d0d0d0;
}
*{margin:0;padding:0;box-sizing:border-box}
html,body{width:708px;height:1200px;overflow:hidden}
body{position:relative;background:var(--page-grey) radial-gradient(circle at 30% 20%,#b3b3b3,#9d9d9d);font-family:"Lato",sans-serif;color:var(--text)}
a{text-decoration:none}
.column{position:absolute;left:78px;top:0;width:552px;height:1033px;background:linear-gradient(160deg,#ecd9a6,var(--parchment) 40%,var(--parchment-dark));border-left:2px solid #3a2a12;border-right:2px solid #3a2a12}
.brand{position:absolute;left:86px;top:14px;display:flex;align-items:center;gap:8px}
.brand-dot{width:30px;height:30px;border-radius:50%;background:var(--brown)}
.brand-name{font-family:"Rufina",serif;font-weight:400;color:var(--brown);font-size:20px;line-height:18px;letter-spacing:.5px}
.contact{position:absolute;top:31px;display:flex;align-items:center;gap:6px}
.contact .icon{width:18px;height:18px;border-radius:50%;background:var(--brown);display:flex;align-items:center;justify-content:center}
.contact small{display:block;font-size:6px;font-style:italic;color:var(--ink)}
.contact span{font-size:8px;color:var(--ink)}
.nav{position:absolute;left:20px;top:76px;width:668px;height:34px}
.nav ul{position:absolute;left:50px;top:2px;width:568px;height:28px;list-style:none;font-size:7.5px;color:var(--white);letter-spacing:.3px}
.nav li{position:absolute;top:9px}
.slider{position:absolute;left:86px;top:118px;width:536px;height:220px;background:var(--white)}
.slide-photo{position:absolute;left:5px;top:4px;width:526px;height:211px;background:linear-gradient(180deg,#7a817a 0%,#7f857d 50%,#8a3a3a 75%,#8c1c22 100%)}
.portrait{position:absolute;left:122px;top:158px;width:140px;height:140px;border-radius:50%;background:#a88a78;border:2px solid #e3c97a}
.slide-title{position:absolute;left:276px;top:168px;font-family:"Playball",serif;font-weight:400;color:var(--white);font-size:27px;line-height:29px}
.slide-copy{position:absolute;left:276px;top:232px;font-size:7px;color:#eee;line-height:10px;width:150px}
.btn{position:absolute;background:#1e1e1e;color:var(--white);font-size:7px;font-weight:700;display:flex;align-items:center;justify-content:center;gap:4px;border:1px solid #555;border-radius:2px}
.arrow{position:absolute;top:217px;width:20px;height:20px;border-radius:50%;background:var(--brown);border:2px solid var(--white)}
.content{position:absolute;left:86px;top:346px;width:536px;height:686px;background:var(--white)}
.section-title{position:absolute;font-family:"Rufina",serif;color:var(--ink);font-weight:400}
.about-text{position:absolute;left:92px;top:397px;width:524px;font-size:7.2px;line-height:12px;text-align:center}
.authority-text{position:absolute;left:91px;top:519px;width:380px;font-size:7.2px;line-height:12px}
.review-table{position:absolute;left:90px;top:582px;width:386px;border-collapse:collapse;font-size:6.2px;font-weight:400;color:var(--white)}
.review-table th{background:var(--table-head);height:24px;text-align:left;font-weight:400;font-size:7px;padding:0 5px;line-height:8px;border-right:1px solid #444}
.review-table td{background:var(--row);height:63.6px;border-right:1px solid var(--row-line);border-top:1px solid var(--row-line);padding:0 5px;vertical-align:middle;line-height:9.2px}
.review-table tr:nth-child(even) td{background:var(--row-alt)}
.product-photo{width:51px;height:36px;background:linear-gradient(135deg,#7d6a48,#3d3a28);border:1px solid #e9dcc4}
.product-name{font-weight:700;font-size:6.5px;line-height:7px;margin-top:2px}
.buy{background:#1e1e1e;color:var(--white);font-size:7px;font-weight:700;text-align:center;width:59px;height:18px;line-height:18px;border-radius:2px;margin:auto}
.ratings div{display:flex;justify-content:space-between;padding-right:6px}
.blog-list{position:absolute;left:490px;top:519px;width:126px;list-style:none}
.blog-list li{display:flex;gap:5px;height:61.3px;border-bottom:1px solid #e5e5e5;padding-top:1px}
.blog-thumb{flex:none;width:43px;height:37px;background:linear-gradient(135deg,#d7b8a1,#8a5a4a 55%,#c63b6b)}
.blog-list time{display:block;font-size:6px;font-style:italic;color:var(--brown)}
.blog-list p{font-size:6px;line-height:10px;color:#444}
.blog-list p b{color:var(--brown);font-weight:400}
.footer{position:absolute;left:0;top:1033px;width:708px;height:145px;background:var(--black);color:var(--footer-text)}
.footer h3{position:absolute;top:14px;font-family:"Rufina",serif;font-size:9px;font-weight:400;color:var(--white);padding-bottom:7px;border-bottom:1px solid #444}
.quick-links{position:absolute;left:101px;top:43px;list-style:none;font-size:7px;line-height:15.2px;color:var(--footer-text)}
.field{position:absolute;left:221px;width:108px;background:var(--white);color:#666;font-size:5.5px;padding:3px 4px}
.social{position:absolute;left:376px;top:40px;list-style:none;width:65px}
.social li{display:flex;align-items:center;gap:5px;font-size:6.5px;height:25.5px;border-bottom:1px solid #333}
.social i{width:11px;height:11px;background:#555;display:block}
.footer-brand{position:absolute;left:490px;top:52px;display:flex;align-items:center;gap:8px}
.footer-brand .brand-dot{width:34px;height:34px;background:var(--footer-brand)}
.footer-brand .brand-name{color:var(--footer-brand);font-size:20px;line-height:19px}
.copyright{position:absolute;left:0;top:1178px;width:708px;height:22px;background:var(--brown);color:var(--white);font-size:6.2px;text-align:center;line-height:22px}
</style>
</head>
<body>
<div class="column"></div>

<header>
  <div class="brand"><div class="brand-dot"></div><div class="brand-name">TOP WHISKER<br>TONIC</div></div>
  <div class="contact" style="left:416px">
    <div class="icon"><svg width="9" height="9" viewBox="0 0 10 10"><path d="M2 1l2 2-1 1.3c.7 1.4 1.7 2.4 3 3L7.3 6l2 2-1.3 1.5C4.5 9.2 .8 5.5.5 2z" fill="#fff"/></svg></div>
    <div><small>Call Us:</small><span>123-456-7890</span></div>
  </div>
  <div class="contact" style="left:508px">
    <div class="icon"><svg width="10" height="8" viewBox="0 0 10 8"><rect x=".5" y=".5" width="9" height="7" fill="#fff"/><path d="M.5.5L5 4.5 9.5.5" stroke="#93601f" fill="none"/></svg></div>
    <div><small>Email Id :</small><span>inquiry@sitename.com</span></div>
  </div>
  <nav class="nav">
    <svg width="668" height="34" viewBox="0 0 668 34">
      <path d="M0 12h52v18H0l10-9z" fill="#7a4c17"/>
      <path d="M668 12h-52v18h52l-10-9z" fill="#7a4c17"/>
      <rect x="50" y="2" width="568" height="28" fill="#93601f"/>
      <line x1="52" y1="5" x2="616" y2="5" stroke="#c69a5a" stroke-dasharray="2 2"/>
      <line x1="52" y1="27" x2="616" y2="27" stroke="#c69a5a" stroke-dasharray="2 2"/>
    </svg>
    <ul>
      <li style="left:43px">HOME</li>
      <li style="left:127px">ABOUT ME</li>
      <li style="left:226px">BEARD OIL REVIEW METHODOLOGY</li>
      <li style="left:411px">OUR CHARTER</li>
      <li style="left:519px">BLOG</li>
    </ul>
  </nav>
</header>

<section class="slider">
  <div class="slide-photo" role="img" aria-label="Product photo: beard oil bottle on a plaid blanket"></div>
</section>
<div class="portrait" role="img" aria-label="Circular portrait of Delvin Marsk"></div>
<h2 class="slide-title">Timberline<br>Beard Oil</h2>
<p class="slide-copy">Lorem ipsum dolor sit amet, consectetuer adipiscing elit, sed diam nonummy nibh.</p>
<a class="btn" style="left:278px;top:267px;width:60px;height:17px">BUY NOW</a>
<div class="arrow" style="left:77px"><svg width="16" height="16" viewBox="0 0 16 16"><path d="M9.5 4.5L6 8l3.5 3.5" stroke="#fff" stroke-width="1.6" fill="none"/></svg></div>
<div class="arrow" style="left:608px"><svg width="16" height="16" viewBox="0 0 16 16"><path d="M6.5 4.5L10 8l-3.5 3.5" stroke="#fff" stroke-width="1.6" fill="none"/></svg></div>

<main class="content"></main>
<h2 class="section-title" style="left:0;width:708px;text-align:center;top:355px;font-size:18px">About Me</h2>
<svg style="position:absolute;left:101px;top:377px" width="508" height="14" viewBox="0 0 508 14">
  <line x1="0" y1="7" x2="244" y2="7" stroke="#aaa" stroke-width=".7"/>
  <line x1="264" y1="7" x2="508" y2="7" stroke="#aaa" stroke-width=".7"/>
  <circle cx="254" cy="9" r="3.5" fill="#93601f"/>
</svg>
<p class="about-text">Lorem ipsum dolor sit amet, consectetuer adipiscing elit, sed diam nonummy nibh euismod tincidunt ut laoreet dolore magna aliquam erat volutpat. Ut wisi enim ad minim veniam, quis nostrud exerci tation ullamcorper suscipit lobortis nisl ut aliquip ex ea commodo consequat. Duis autem vel eum iriure dolor in hendrerit in vulputate velit esse molestie consequat, vel illum dolore eu feugiat nulla .</p>
<a class="btn" style="left:323px;top:440px;width:62px;height:18px">READ MORE</a>

<h2 class="section-title" style="left:90px;top:477px;font-size:17.5px">The World’s #1 Beard Oil Authority</h2>
<svg style="position:absolute;left:90px;top:504px" width="383" height="4"><rect y="1" width="383" height="1" fill="#aaa"/><rect width="70" height="2.5" fill="#333"/></svg>
<p class="authority-text">Here is the master list of beard oils reviewed to date. You can link directly to the corresponding review by clicking on the name of the beard oil. In accordance with our charter, we are actively working to locate and review every single beard oil available on the planet Earth.</p>

<table class="review-table">
  <thead><tr>
    <th style="width:68px">Product Photo &amp; Name</th>
    <th style="width:71px">Origin, Base Oil &amp; Scent</th>
    <th style="width:90px">Reviews</th>
    <th style="width:85px">Aroma, Value, Overall, Therapeutic Affect,</th>
    <th></th>
  </tr></thead>
  <tbody>
    <tr><td><div class="product-photo" role="img" aria-label="Timberline bottle photo"></div><div class="product-name">Timberline</div></td><td>O : &nbsp;Lorem Ispum<br><br>B : &nbsp;Lorem Ispum<br><br>S : &nbsp;Lorem Ispum</td><td>Lorem ipsum dolot amet, consectetuer adiping elit, sed diam nonummuismod tincidunt ut laore dolore magna aliquam.</td><td class="ratings"><div><span>Aroma :</span>7</div><div><span>Value :</span>3</div><div><span>Overall :</span>6</div><div><span>Therapeutic Affect :</span>1</div></td><td><div class="buy">BUY NOW</div></td></tr>
    <tr><td><div class="product-photo" role="img" aria-label="Axeman bottle photo"></div><div class="product-name">Axeman</div></td><td>O : &nbsp;Lorem Ispum<br><br>B : &nbsp;Lorem Ispum<br><br>S : &nbsp;Lorem Ispum</td><td>Lorem ipsum dolot amet, consectetuer adiping elit, sed diam nonummuismod tincidunt ut laore dolore magna aliquam.</td><td class="ratings"><div><span>Aroma :</span>7</div><div><span>Value :</span>3</div><div><span>Overall :</span>6</div><div><span>Therapeutic Affect :</span>1</div></td><td><div class="buy">BUY NOW</div></td></tr>
    <tr><td><div class="product-photo" role="img" aria-label="Chinwood Beard Oil bottles photo"></div><div class="product-name">Chinwood Beard Oil</div></td><td>O : &nbsp;Lorem Ispum<br><br>B : &nbsp;Lorem Ispum<br><br>S : &nbsp;Lorem Ispum</td><td>Lorem ipsum dolot amet, consectetuer adiping elit, sed diam nonummuismod tincidunt ut laore dolore magna aliquam.</td><td class="ratings"><div><span>Aroma :</span>7</div><div><span>Value :</span>3</div><div><span>Overall :</span>6</div><div><span>Therapeutic Affect :</span>1</div></td><td><div class="buy">BUY NOW</div></td></tr>
    <tr><td><div class="product-photo" role="img" aria-label="Outback Bristle Oil bottle photo"></div><div class="product-name">Outback Bristle Oil</div></td><td>O : &nbsp;Lorem Ispum<br><br>B : &nbsp;Lorem Ispum<br><br>S : &nbsp;Lorem Ispum</td><td>Lorem ipsum dolot amet, consectetuer adiping elit, sed diam nonummuismod tincidunt ut laore dolore magna aliquam.</td><td class="ratings"><div><span>Aroma :</span>7</div><div><span>Value :</span>3</div><div><span>Overall :</span>6</div><div><span>Therapeutic Affect :</span>1</div></td><td><div class="buy">BUY NOW</div></td></tr>
    <tr><td><div class="product-photo" role="img" aria-label="Timberline bottle photo"></div><div class="product-name">Timberline</div></td><td>O : &nbsp;Lorem Ispum<br><br>B : &nbsp;Lorem Ispum<br><br>S : &nbsp;Lorem Ispum</td><td>Lorem ipsum dolot amet, consectetuer adiping elit, sed diam nonummuismod tincidunt ut laore dolore magna aliquam.</td><td class="ratings"><div><span>Aroma :</span>7</div><div><span>Value :</span>3</div><div><span>Overall :</span>6</div><div><span>Therapeutic Affect :</span>1</div></td><td><div class="buy">BUY NOW</div></td></tr>
    <tr><td><div class="product-photo" role="img" aria-label="Axeman bottle photo"></div><div class="product-name">Axeman</div></td><td>O : &nbsp;Lorem Ispum<br><br>B : &nbsp;Lorem Ispum<br><br>S : &nbsp;Lorem Ispum</td><td>Lorem ipsum dolot amet, consectetuer adiping elit, sed diam nonummuismod tincidunt ut laore dolore magna aliquam.</td><td class="ratings"><div><span>Aroma :</span>7</div><div><span>Value :</span>3</div><div><span>Overall :</span>6</div><div><span>Therapeutic Affect :</span>1</div></td><td><div class="buy">BUY NOW</div></td></tr>
  </tbody>
</table>
<a class="btn" style="left:245px;top:1000px;width:69px;height:19px"><svg width="9" height="9" viewBox="0 0 10 10"><path d="M8.5 5A3.5 3.5 0 1 1 7 2.2" stroke="#fff" stroke-width="1.6" fill="none"/><path d="M6 0.5l2.5 2-2.8 1z" fill="#fff"/></svg>LORD MORE</a>

<h2 class="section-title" style="left:490px;top:477px;font-size:17.5px">Blog Posts</h2>
<svg style="position:absolute;left:490px;top:504px" width="126" height="4"><rect y="1" width="126" height="1" fill="#aaa"/><rect width="40" height="2.5" fill="#333"/></svg>
<ul class="blog-list">
  <li><div class="blog-thumb" role="img" aria-label="Blog post photo"></div><div><time>11 Feb 2016</time><p>Duis autem vel eum iriure dolor in hendreri inmo vulputate velit ... <b>[+]</b></p></div></li>
  <li><div class="blog-thumb" role="img" aria-label="Blog post photo"></div><div><time>11 Feb 2016</time><p>Duis autem vel eum iriure dolor in hendreri inmo vulputate velit ... <b>[+]</b></p></div></li>
  <li><div class="blog-thumb" role="img" aria-label="Blog post photo"></div><div><time>11 Feb 2016</time><p>Duis autem vel eum iriure dolor in hendreri inmo vulputate velit ... <b>[+]</b></p></div></li>
  <li><div class="blog-thumb" role="img" aria-label="Blog post photo"></div><div><time>11 Feb 2016</time><p>Duis autem vel eum iriure dolor in hendreri inmo vulputate velit ... <b>[+]</b></p></div></li>
  <li><div class="blog-thumb" role="img" aria-label="Blog post photo"></div><div><time>11 Feb 2016</time><p>Duis autem vel eum iriure dolor in hendreri inmo vulputate velit ... <b>[+]</b></p></div></li>
  <li><div class="blog-thumb" role="img" aria-label="Blog post photo"></div><div><time>11 Feb 2016</time><p>Duis autem vel eum iriure dolor in hendreri inmo vulputate velit ... <b>[+]</b></p></div></li>
  <li><div class="blog-thumb" role="img" aria-label="Blog post photo"></div><div><time>11 Feb 2016</time><p>Duis autem vel eum iriure dolor in hendreri inmo vulputate velit ... <b>[+]</b></p></div></li>
  <li style="border:0"><div class="blog-thumb" role="img" aria-label="Blog post photo"></div><div><time>11 Feb 2016</time><p>Duis autem vel eum iriure dolor in hendreri inmo vulputate velit ... <b>[+]</b></p></div></li>
</ul>
<a class="btn" style="left:556px;top:1000px;width:60px;height:18px">VIEW ALL</a>

<footer class="footer">
  <h3 style="left:101px;width:74px">Quick Links</h3>
  <ul class="quick-links"><li>Home</li><li>About Us</li><li>Beard Oil Review</li><li>Methodology</li><li>Our Charter</li><li>Blogs</li></ul>
  <h3 style="left:222px;width:107px">Quick Inquiry</h3>
  <div class="field" style="top:40px;height:15px">Name</div>
  <div class="field" style="top:60px;height:15px">Email</div>
  <div class="field" style="top:80px;height:29px">Message</div>
  <div class="btn" style="left:221px;top:116px;width:37px;height:14px;background:#3a3a3a">Submit</div>
  <h3 style="left:376px;top:12px;width:65px">Follow Us On</h3>
  <ul class="social">
    <li><i></i>Pagebook</li>
    <li><i></i>Chirper</li>
    <li><i></i>Vidstream</li>
    <li style="border:0"><i></i>Linkwork</li>
  </ul>
  <div class="footer-brand"><div class="brand-dot"></div><div class="brand-name">TOP WHISKER<br>TONIC</div></div>
</footer>
<div class="copyright">Copyright 2016 Top Whisker Tonic. All Rights Reserved.</div>
</body>
</html>
```